Pawn & Gun store business card design

Hello! We would like a new business card design for our pawn & gun store. We loan money on items of value and sell firearms, jewelry, electronics & more.

Card will need to have the following information:

Business name - Prairie Nickel Pawn & Gun
Address - 2417 Hwy 53 S. Suite C Wylie, TX 75246
Employees name - Darren Kellum
Phone number - 972-613-8840
Email - PrairieNickelPawn@Mailvera.com
Website - PrairieNickelPawn.com

Somewhere on the card we would like it to say "Offering 10 Month Layaway!" & "We buy & loan on anything of value!". Our main store color is orange (please see logo). Logo does not have to be on the business card but it can be. Would like the back to have an area to write a note on the back. We like vintage things like old coins, collectables, firearms and more so think about this in the design. We want a business card as unique as our store!

Colors

Designer to choose colors to be used in the design.

Requirements
Nice to have
• Vintage Style

```html
<!DOCTYPE html>
<html lang="en">
<head>
<meta charset="utf-8">
<title>Prairie Nickel Pawn &amp; Gun — Business Card</title>
<link rel="stylesheet" href="https://fonts.googleapis.com/css2?family=Oswald:wght@400;500;700&family=Allura&display=swap">
<style>
  :root {
    --backdrop: #a3a3a5;
    --kraft: #d6b88f;
    --ink: #3b2415;
    --orange: #d8601d;
    --rule: 2px solid var(--ink);
  }
  * { box-sizing: border-box; margin: 0; padding: 0; }
  html, body { width: 1200px; height: 800px; overflow: hidden; }
  body {
    background: var(--backdrop);
    display: flex; align-items: center; justify-content: center; gap: 40px;
    font-family: "Oswald", sans-serif; color: var(--ink);
  }
  .card {
    width: 540px; height: 310px;
    background: var(--kraft);
    border-bottom: 3px solid var(--orange);
    padding: 14px;
    box-shadow: 0 6px 16px rgba(0,0,0,.25);
  }
  .frame { width: 100%; height: 100%; border: var(--rule); }

  /* Front */
  .front .frame {
    display: grid;
    grid-template-columns: 105px 105px 1fr;
    grid-template-rows: 116px 62px 1fr;
  }
  .name {
    grid-column: 1 / 4; border-bottom: var(--rule);
    display: flex; align-items: center; justify-content: center;
    font-weight: 700; font-size: 72px; letter-spacing: 1px;
    text-transform: uppercase; line-height: 1; white-space: nowrap; overflow: hidden;
  }
  .phone {
    grid-column: 1 / 3; background: var(--orange);
    border-right: var(--rule); border-bottom: var(--rule);
    display: flex; align-items: center; justify-content: center;
    font-weight: 700; font-size: 32px; white-space: nowrap;
  }
  .web {
    background: var(--orange); border-bottom: var(--rule);
    display: flex; flex-direction: column; justify-content: center; padding-left: 14px;
    font-size: 15px; font-weight: 500; letter-spacing: .5px; line-height: 1.3;
    text-transform: uppercase; white-space: nowrap;
  }
  .icon-cell { display: flex; align-items: center; justify-content: center; border-right: var(--rule); }
  .icon-art { width: 56px; height: 42px; background: #8a6a4c; border-radius: 3px; }
  .tagline {
    display: flex; flex-direction: column; justify-content: center; align-items: flex-start;
    padding-left: 14px; white-space: nowrap;
  }
  .layaway {
    font-size: 13px; font-weight: 500; letter-spacing: .8px; text-transform: uppercase;
    display: flex; align-items: center; gap: 8px;
  }
  .layaway::before, .layaway::after { content: ""; height: 1px; width: 20px; background: var(--ink); }
  .slogan { font-family: "Allura", cursive; font-size: 20px; margin-top: 2px; }

  /* Back */
  .back .frame {
    display: flex; flex-direction: column; align-items: center; justify-content: center; gap: 10px;
  }
  .brand { display: flex; align-items: center; gap: 12px; }
  .brand-dot { width: 22px; height: 22px; border-radius: 50%; background: var(--orange); }
  .brand-name { font-weight: 700; font-size: 30px; letter-spacing: 1px; text-transform: uppercase; }
  .address { font-size: 13px; font-weight: 500; letter-spacing: 1px; text-transform: uppercase; }
</style>
</head>
<body>
  <section class="card front" aria-label="Card front">
    <div class="frame">
      <h1 class="name">Darren Kellum</h1>
      <div class="phone">972-613-8840</div>
      <div class="web">
        <span>PrairieNickelPawn@Mailvera.com</span>
        <span>www.PrairieNickelPawn.com</span>
      </div>
      <div class="icon-cell"><div class="icon-art" role="img" aria-label="Crossed vintage revolvers illustration"></div></div>
      <div class="icon-cell"><div class="icon-art" role="img" aria-label="Diamond illustration"></div></div>
      <div class="tagline">
        <p class="layaway">Offering 10 Month Layaway</p>
        <p class="slogan">We buy &amp; loan on anything of value</p>
      </div>
    </div>
  </section>

  <section class="card back" aria-label="Card back">
    <div class="frame">
      <div class="brand">
        <span class="brand-dot"></span>
        <span class="brand-name">Prairie Nickel Pawn</span>
      </div>
      <p class="address">2417 Hwy 53 S. Suite C · Wylie, TX 75246</p>
    </div>
  </section>
</body>
</html>
```